Marlowe Crest Realty business card design

Looking for an upscale and clean business card design and updated logo. I sell to a very high-end south Florida real estate market.
Target Market(s)
High-end real estate in south Florida real estate market
Industry/Entity Type
Real Estate Agent
Contact Information for Business Card
Marlowe Crest Realty, Inc
738 West Pinecrest Ave, Suite 410/510, Fort Lauderdale, FL 33308
Gary Whitlock - Broker/Owner
954-327-8846 Direct
garyshomes@quellmail.com
Website: DwellTarrowBay.com
Font styles to use
Other font styles liked:
- Copperplate Gothic, Georgia, etc.
Requirements
Must have
- My photo, company name, my name and title, all info stated in Details above
Nice to have
- Luxury home design element, waterfront

```html
<!DOCTYPE html>
<html lang="en">
<head>
<meta charset="utf-8">
<title>Marlowe Crest Realty – Business Card</title>
<link rel="stylesheet" href="https://fonts.googleapis.com/css2?family=Cormorant+Garamond:wght@500&family=Cinzel:wght@600&family=Montserrat:wght@400;500&display=swap">
<style>
  :root {
    --canvas: #e6e4e0;
    --card: #151517;
    --card-edge: #1d1d20;
    --gold: #f4c531;
    --gold-deep: #c9a229;
    --white: #f5f5f5;
    --ink: #1a1a1a;
    --photo-light: #e9e9e9;
    --photo-mid: #8a8a8a;
  }
  * { margin: 0; padding: 0; box-sizing: border-box; }
  html, body { width: 1200px; height: 900px; overflow: hidden; }
  body {
    background: var(--canvas);
    display: flex;
    flex-direction: column;
    align-items: center;
    justify-content: center;
    gap: 36px;
  }
  .card {
    position: relative;
    width: 720px;
    height: 411px;
    background: var(--card);
    overflow: hidden;
    box-shadow: 0 10px 28px rgba(0,0,0,.28);
  }

  /* Front */
  .card-front .brand {
    position: absolute;
    left: 50%; top: 50%;
    transform: translate(-50%, -50%);
    display: flex;
    align-items: center;
    gap: 22px;
  }
  .brand-dot {
    width: 58px; height: 58px;
    border-radius: 50%;
    background: var(--gold);
    flex: none;
  }
  .brand-name {
    font-family: "Cormorant Garamond", Georgia, serif;
    font-weight: 500;
    font-size: 40px;
    line-height: 1.05;
    color: var(--white);
  }

  /* Back */
  .portrait {
    position: absolute;
    right: 0; top: 0;
    width: 380px; height: 100%;
    background: linear-gradient(90deg, var(--card) 0%, var(--photo-mid) 40%, var(--photo-light) 100%);
  }
  .card-back .brand-small {
    position: absolute;
    left: 48px; top: 40px;
    display: flex;
    align-items: center;
    gap: 10px;
  }
  .brand-small .brand-dot { width: 34px; height: 34px; }
  .brand-small .brand-name { font-size: 17px; }
  .name-band {
    position: absolute;
    left: 0; top: 118px;
    width: 560px; height: 82px;
    background: linear-gradient(90deg, var(--gold) 0%, var(--gold) 50%, var(--gold-deep) 75%, rgba(201,162,41,0) 100%);
    padding: 10px 0 0 48px;
  }
  .agent-name {
    font-family: "Cinzel", Georgia, serif;
    font-weight: 600;
    font-size: 34px;
    letter-spacing: 2px;
    color: var(--white);
    line-height: 1.1;
  }
  .agent-title {
    font-family: "Montserrat", Arial, sans-serif;
    font-size: 15px;
    color: var(--ink);
    margin-top: 4px;
  }
  .details {
    position: absolute;
    left: 48px; top: 214px;
    font-family: "Montserrat", Arial, sans-serif;
    font-weight: 500;
    font-size: 14px;
    line-height: 1.32;
    color: var(--white);
  }
  .company { color: var(--gold); }
  .contact-list { list-style: none; margin-top: 10px; }
  .contact-list li { display: flex; align-items: center; gap: 10px; }
  .contact-list svg { width: 14px; height: 14px; fill: var(--gold); flex: none; }
  .accent { color: var(--gold); }
</style>
</head>
<body>

<section class="card card-front">
  <div class="brand">
    <span class="brand-dot"></span>
    <div class="brand-name">Marlowe Crest<br>Realty, Inc.</div>
  </div>
</section>

<section class="card card-back">
  <div class="portrait" role="img" aria-label="Black and white portrait photo of the broker in a checked blazer"></div>

  <div class="brand-small">
    <span class="brand-dot"></span>
    <div class="brand-name">Marlowe Crest<br>Realty, Inc.</div>
  </div>

  <div class="name-band">
    <div class="agent-name">GARY WHITLOCK</div>
    <div class="agent-title">Broker/Owner</div>
  </div>

  <div class="details">
    <div class="company">Marlowe Crest Realty, Inc</div>
    <div>738 West Pinecrest Ave,<br>Suite 410/510,<br>Fort Lauderdale, FL 33308</div>
    <ul class="contact-list">
      <li>
        <svg viewBox="0 0 24 24"><path d="M6.6 10.8a15 15 0 0 0 6.6 6.6l2.2-2.2a1 1 0 0 1 1-.25 11.4 11.4 0 0 0 3.6.57 1 1 0 0 1 1 1V20a1 1 0 0 1-1 1A17 17 0 0 1 3 4a1 1 0 0 1 1-1h3.5a1 1 0 0 1 1 1c0 1.25.2 2.45.57 3.57a1 1 0 0 1-.25 1z"/></svg>
        954-327-8846
      </li>
      <li>
        <svg viewBox="0 0 24 24"><path d="M2 5h20v14H2z M2 5l10 8 10-8" fill="none" stroke="#f4c531" stroke-width="2.4"/></svg>
        garyshomes@quellmail.com
      </li>
      <li>
        <svg viewBox="0 0 24 24"><circle cx="12" cy="12" r="9" fill="none" stroke="#f4c531" stroke-width="2.4"/><path d="M3 12h18M12 3c3 3 3 15 0 18M12 3c-3 3-3 15 0 18" fill="none" stroke="#f4c531" stroke-width="1.8"/></svg>
        <span>www.<span class="accent">DwellTarrowBay</span>.com</span>
      </li>
    </ul>
  </div>
</section>

</body>
</html>
```